Website for vegan focused blog

A website is needed so that I can launch my new blog in Dubai. It will be mainly vegan focused but also lifestyle based. Wordpress based- i started to build a site on Wordpress but design is not my forte ;)
Main content on the site will be; my recipes, reviews of products/restaurants, lifestyle posts and travel.
For this I ask for a homepage design, a recipe design page that includes a recipe card and a generic page for posts that can show pictures and videos. Also a contact me page.
Main headers should be: Home, Recipes and happy for suggestions.
Must look clean and neat but appealing, happy for minimalist look. I like pink and grey colours. Must be Wordpress compatible.
Have attached a couple of example posts for reference
Must have social links etc.
name of blog is: Maren by the dunes
Other blogs I like are: https://quietladleoven.com/ https://wellfernkitchen.com/ https://wellfernkitchen.com/ https://www.ohladycakes.com/https://beetsatsupper.com/ https://dorintalve.com/

Target Market(s)

Residents in the UAE. General individuals interested in vegan meals, plant based nutrition, travel and reviews.

Number of Pages Required

4 page

Colors
eea4c8
eda3c7
f9d9e8
dbdbdb
aaaaaa
d5d5d5

Requirements
Must have
• Recipe page- must include recipe card plug in option
• Social media integration
• Email sign ups

```html
<!DOCTYPE html>
<html lang="en">
<head>
<meta charset="utf-8">
<title>Maren by the dunes — Mushroom Steak</title>
<link rel="stylesheet" href="https://fonts.googleapis.com/css2?family=Lato:ital,wght@0,400;0,700;1,400&family=Playfair+Display:ital,wght@0,400;1,400&display=swap">
<style>
  :root {
    --pink: #eea4c8;
    --pink-soft: #f9d9e8;
    --pink-button: #f7c3dc;
    --line: #dbdbdb;
    --line-soft: #e6e6e6;
    --grey: #aaaaaa;
    --text: #3a3a3a;
    --text-soft: #6a6a6a;
    --white: #ffffff;
  }
  * { box-sizing: border-box; margin: 0; padding: 0; }
  html, body { width: 1200px; height: 930px; overflow: hidden; background: var(--white); }
  body { position: relative; font-family: "Lato", sans-serif; color: var(--text); }

  .site-header { position: absolute; left: 0; top: 0; width: 1200px; height: 152px; }
  .brand {
    position: absolute; left: 0; width: 1200px; top: 38px; text-align: center;
    font-family: "Playfair Display", serif; font-weight: 400; font-size: 31px;
    color: var(--pink); letter-spacing: 0.5px;
  }
  .main-nav {
    position: absolute; left: 0; top: 114px; width: 1200px; height: 39px;
    border-top: 1px solid var(--line-soft); border-bottom: 1px solid var(--line-soft);
  }
  .main-nav a {
    position: absolute; top: 12px; font-family: "Playfair Display", serif; font-style: italic;
    font-size: 10.5px; color: #333; text-decoration: none; letter-spacing: 0.7px;
    white-space: nowrap;
  }
  .search-icon { position: absolute; left: 954px; top: 13px; }

  .post { position: absolute; left: 234px; top: 182px; width: 506px; }
  .post-title {
    text-align: center; font-family: "Playfair Display", serif; font-weight: 400;
    font-size: 19px; color: var(--pink); margin-top: 17px; line-height: 22px;
  }
  .post-rule { width: 26px; height: 1px; background: #555; margin: 13px auto 0; }
  .post-date {
    text-align: center; font-size: 7px; letter-spacing: 0.8px; color: var(--text-soft);
    margin-top: 12px;
  }
  .post-photo {
    margin-top: 19px; width: 506px; height: 352px;
    background: radial-gradient(ellipse at 60% 35%, #c9472f 0%, transparent 32%),
                radial-gradient(ellipse at 60% 60%, #4a2a22 0%, #3b2620 35%, transparent 60%),
                linear-gradient(90deg, #1f3a1c 0%, #2c4a25 38%, #efece8 60%, #f5f3f0 100%);
  }
  .post-body { margin-top: 28px; font-size: 9.2px; line-height: 15.2px; color: var(--text); }
  .post-body p + p { margin-top: 14.6px; }

  .post-meta {
    position: absolute; left: 234px; top: 845px; width: 506px; height: 39px;
    border-top: 1px solid var(--line); border-bottom: 1px solid var(--line);
    font-size: 7px; color: var(--text);
  }
  .post-meta .comments { position: absolute; left: 0; top: 15px; letter-spacing: 0.3px; }
  .post-meta .divider { position: absolute; left: 76px; top: 6px; width: 1px; height: 27px; background: var(--line); }
  .post-meta .tags { position: absolute; left: 93px; top: 15px; letter-spacing: 0.3px; }
  .post-meta .tags em { font-style: italic; color: var(--grey); letter-spacing: 0; }
  .share { position: absolute; left: 426px; top: 16px; display: flex; gap: 11px; }
  .share span { width: 7px; height: 7px; border-radius: 50%; background: #444; display: block; }

  .widget {
    position: absolute; left: 778px; width: 188px; border: 1px solid var(--line-soft);
    background: var(--white);
  }
  .widget-title {
    font-family: "Playfair Display", serif; font-style: italic; font-weight: 400;
    font-size: 11.5px; color: var(--pink); position: absolute; left: 11px; top: 17px;
    white-space: nowrap;
  }
  .about { top: 182px; height: 242px; }
  .about-photo {
    position: absolute; left: 11px; top: 46px; width: 165px; height: 97px;
    background: linear-gradient(180deg, #c7a58a 0%, #8a7a73 35%, #3d4148 60%, #2b2c2e 100%);
  }
  .about-text {
    position: absolute; left: 10px; top: 156px; width: 166px; text-align: center;
    font-size: 8px; line-height: 12.5px; color: var(--text);
  }
  .about-more { position: absolute; left: 0; width: 188px; top: 222px; text-align: center; font-size: 8px; font-style: italic; color: var(--text); }
  .about-more span { color: var(--grey); }

  .follow { top: 450px; height: 93px; }
  .social-list { position: absolute; left: 23px; top: 48px; display: flex; gap: 9px; }
  .social-list span {
    width: 21px; height: 21px; border-radius: 50%; background: var(--pink);
    border: 2px solid var(--pink-soft); display: block;
  }

  .newsletter { top: 569px; height: 141px; }
  .email-field {
    position: absolute; left: 11px; top: 47px; width: 165px; height: 31px;
    border: 1px solid var(--line); font-size: 8px; font-style: italic; color: #bbb;
    padding: 11px 10px;
  }
  .subscribe-button {
    position: absolute; left: 11px; top: 90px; width: 165px; height: 28px;
    background: var(--pink-button); color: var(--white); font-size: 7.5px; letter-spacing: 0.8px;
    text-align: center; line-height: 28px;
  }

  .photo-feed { top: 738px; height: 220px; }
  .feed-grid { position: absolute; left: 11px; top: 46px; display: grid; grid-template-columns: 80px 80px; gap: 4px; }
  .feed-tile {
    width: 80px; height: 80px;
    background: radial-gradient(ellipse at 65% 20%, #c9472f 0%, transparent 35%),
                radial-gradient(ellipse at 60% 65%, #4a2a22 0%, #3b2620 35%, transparent 62%),
                linear-gradient(90deg, #1f3a1c 0%, #2c4a25 40%, #efece8 68%, #f5f3f0 100%);
  }
</style>
</head>
<body>
  <header class="site-header">
    <div class="brand">Maren by the dunes</div>
    <nav class="main-nav">
      <a href="#" style="left:337px">Home</a>
      <a href="#" style="left:402px">About</a>
      <a href="#" style="left:468px">Recipes</a>
      <a href="#" style="left:542px">Reviews of products</a>
      <a href="#" style="left:678px">Lifestyle</a>
      <a href="#" style="left:757px">Travel</a>
      <a href="#" style="left:826px">Contact</a>
      <svg class="search-icon" width="11" height="11" viewBox="0 0 11 11" aria-label="Search">
        <circle cx="4.6" cy="4.6" r="3.6" fill="none" stroke="#333" stroke-width="1.3"/>
        <line x1="7.3" y1="7.3" x2="10.2" y2="10.2" stroke="#333" stroke-width="1.4"/>
      </svg>
    </nav>
  </header>

  <article class="post">
    <h1 class="post-title">Mushroom Steak</h1>
    <div class="post-rule"></div>
    <div class="post-date">SATURDAY, SEPTEMBER 8, 2018</div>
    <div class="post-photo" role="img" aria-label="Grilled portobello mushroom steak with roasted tomato halves, steamed spinach and a herb dip on a white plate"></div>
    <div class="post-body">
      <p>Steak and vegan don't go in the same sentence BUT trust me on this...a decent sized Portobello shroom cooked just right with a blend of delicious marinade, it has the meatiest texture and its delicious as well oh and did we mention it is completely cruelty free!?</p>
      <p>To get the right texture you need the right tools so I always suggest cooking this on a griddle pan or even on the BBQ to give it that additional boost of flavours.</p>
      <p>When my non vegan friends are looking for something to cook when they have the plant powered team over for dinner, I always use this as a suggestion. The sides can be mixed and matched so in this instance I have used a grilled tomato and a pile of steamed spinach but you can add fries or salad or anything else that would be served alongside a steak. So all in all, it is a very versatile dish.</p>
    </div>
  </article>

  <footer class="post-meta">
    <span class="comments">12 COMMENTS</span>
    <span class="divider"></span>
    <span class="tags">TAGGED : <em>Food, mushroom, balsamic vinegar, olive oil, cumin, paprika, spinach</em></span>
    <div class="share" aria-label="Share links"><span></span><span></span><span></span><span></span><span></span></div>
  </footer>

  <aside>
    <section class="widget about">
      <h2 class="widget-title">About Maren by the dunes</h2>
      <div class="about-photo" role="img" aria-label="Seaside at sunset with a figure standing on the shore beside dark rocks"></div>
      <p class="about-text">On Maren by the dunes, I share some delicious recipes either my own or from other fabulous sites that I have come across, my meal plans, reviews of products and restaurants that I visit and more.</p>
      <div class="about-more">More <span>⟶</span></div>
    </section>

    <section class="widget follow">
      <h2 class="widget-title">Subscribe &amp; Follow</h2>
      <div class="social-list" aria-label="Social links"><span></span><span></span><span></span><span></span><span></span></div>
    </section>

    <section class="widget newsletter">
      <h2 class="widget-title">Newsletter</h2>
      <div class="email-field">Your Email Address</div>
      <div class="subscribe-button">SUBSCRIBE</div>
    </section>

    <section class="widget photo-feed">
      <h2 class="widget-title">Photo Feed</h2>
      <div class="feed-grid">
        <div class="feed-tile" role="img" aria-label="Mushroom steak plate"></div>
        <div class="feed-tile" role="img" aria-label="Mushroom steak plate"></div>
        <div class="feed-tile" role="img" aria-label="Mushroom steak plate"></div>
        <div class="feed-tile" role="img" aria-label="Mushroom steak plate"></div>
      </div>
    </section>
  </aside>
</body>
</html>
```